Business card for medical clinic

I need an upmarket, modern medical/health business card for my clinic

Contact Information for Business Card

name, address, email, qr code

```html
<!DOCTYPE html>
<html lang="en">
<head>
<meta charset="utf-8">
<title>Meridale Health Clinic – Business Card</title>
<link href="https://fonts.googleapis.com/css2?family=Poppins:wght@300;400;600&display=swap" rel="stylesheet">
<style>
  :root {
    --page-bg: #1f1f21;
    --card-bg: #1d1e22;
    --card-bg-deep: #16171a;
    --brand-blue: #1f9bd7;
    --brand-blue-deep: #137fbf;
    --ink-light: #f2f4f6;
    --ink-muted: #c9ced4;
  }
  * { box-sizing: border-box; margin: 0; padding: 0; }
  html, body {
    width: 1200px; height: 780px; overflow: hidden;
    background: var(--page-bg);
    font-family: "Poppins", sans-serif;
  }
  .canvas {
    width: 1200px; height: 780px;
    display: flex; align-items: center; justify-content: center; gap: 40px;
  }
  .card {
    position: relative;
    width: 540px; height: 309px;
    background: var(--card-bg);
    border-radius: 4px;
    overflow: hidden;
    box-shadow: 0 18px 40px rgba(0,0,0,.55);
  }
  .card-swoosh { position: absolute; inset: 0; width: 100%; height: 100%; }

  .holder { position: absolute; left: 58px; top: 30px; }
  .holder-name { font-size: 30px; line-height: 1; letter-spacing: .5px; color: var(--brand-blue); }
  .holder-name .first { font-weight: 600; }
  .holder-name .last { font-weight: 300; color: #3aa8de; }
  .holder-title { margin-top: 8px; margin-left: 60px; font-size: 13px; font-weight: 400; color: var(--ink-light); }

  .brand { display: flex; align-items: center; gap: 10px; }
  .brand-dot { width: 34px; height: 34px; border-radius: 50%; border: 2px solid var(--brand-blue); flex: none; }
  .brand-name { font-weight: 400; color: var(--brand-blue); letter-spacing: 2px; text-transform: uppercase; line-height: 1.25; }
  .front .brand { position: absolute; right: 40px; top: 30px; }
  .front .brand-name { font-size: 13px; }

  .divider { position: absolute; left: 250px; top: 118px; width: 1px; height: 78px; background: var(--brand-blue); transform: rotate(35deg); }

  .contact-list { position: absolute; left: 300px; top: 128px; list-style: none; }
  .contact-list li { display: flex; align-items: center; gap: 9px; font-size: 13px; color: var(--ink-light); line-height: 23px; }
  .contact-list svg { width: 13px; height: 13px; flex: none; fill: var(--brand-blue); }

  .address { position: absolute; left: 22px; bottom: 22px; font-size: 13px; color: var(--ink-light); letter-spacing: .2px; }

  .back { background: var(--card-bg-deep); }
  .back-texture {
    position: absolute; inset: 0;
    background: radial-gradient(ellipse at 75% 40%, #34363b 0%, #202125 45%, #141518 100%);
  }
  .back .brand { position: absolute; left: 50%; top: 50%; transform: translate(-50%, -50%); gap: 14px; }
  .back .brand-dot { width: 52px; height: 52px; border-width: 3px; }
  .back .brand-name { font-size: 20px; }
</style>
</head>
<body>
<main class="canvas">

  <section class="card front" aria-label="Business card front">
    <svg class="card-swoosh" viewBox="0 0 540 309" preserveAspectRatio="none" aria-hidden="true">
      <defs>
        <linearGradient id="bandFill" x1="0" y1="0" x2="1" y2="0">
          <stop offset="0" stop-color="#2aa6de"/>
          <stop offset=".75" stop-color="#1a8fcc"/>
          <stop offset=".92" stop-color="#6fb6dc"/>
          <stop offset="1" stop-color="#e8f1f7"/>
        </linearGradient>
        <linearGradient id="edgeGlow" x1="0" y1="0" x2="1" y2="0">
          <stop offset="0" stop-color="#eef5fa"/>
          <stop offset=".12" stop-color="#2aa6de"/>
          <stop offset="1" stop-color="#1f9bd7"/>
        </linearGradient>
      </defs>
      <path d="M0,232 C150,268 360,268 540,246 L540,309 L0,309 Z" fill="url(#bandFill)"/>
      <path d="M0,222 C150,262 360,262 540,238" fill="none" stroke="url(#edgeGlow)" stroke-width="5"/>
      <path d="M8,212 C150,254 360,254 520,232" fill="none" stroke="#2b5f82" stroke-width="1.5"/>
    </svg>

    <div class="holder">
      <p class="holder-name"><span class="first">Marta</span> <span class="last">Lindqvist</span></p>
      <p class="holder-title">Founder &amp; CEO</p>
    </div>

    <div class="brand">
      <span class="brand-dot"></span>
      <span class="brand-name">Meridale Health<br>Clinic</span>
    </div>

    <span class="divider"></span>

    <ul class="contact-list">
      <li><svg viewBox="0 0 24 24"><path d="M6.6 10.8a15.1 15.1 0 0 0 6.6 6.6l2.2-2.2a1 1 0 0 1 1-.25 11.4 11.4 0 0 0 3.6.57 1 1 0 0 1 1 1V20a1 1 0 0 1-1 1A17 17 0 0 1 3 4a1 1 0 0 1 1-1h3.5a1 1 0 0 1 1 1c0 1.25.2 2.45.57 3.6a1 1 0 0 1-.25 1z"/></svg>(555) 214-7730</li>
      <li><svg viewBox="0 0 24 24"><path d="M3 5h18a1 1 0 0 1 1 1v12a1 1 0 0 1-1 1H3a1 1 0 0 1-1-1V6a1 1 0 0 1 1-1zm9 7.5L4 7.3V8l8 5.2L20 8v-.7z"/></svg>info@meridalehealth.com</li>
      <li><svg viewBox="0 0 24 24"><path d="M12 2a10 10 0 1 0 0 20 10 10 0 0 0 0-20zm6.9 6h-3a15.6 15.6 0 0 0-1.4-3.6A8 8 0 0 1 18.9 8zM12 4a14 14 0 0 1 1.9 4h-3.8A14 14 0 0 1 12 4zM4.3 14a8 8 0 0 1 0-4h3.4a16 16 0 0 0 0 4zm.8 2h3a15.6 15.6 0 0 0 1.4 3.6A8 8 0 0 1 5.1 16zM8 8H5.1a8 8 0 0 1 4.3-3.6A15.6 15.6 0 0 0 8 8zm4 12a14 14 0 0 1-1.9-4h3.8A14 14 0 0 1 12 20zm2.3-6H9.7a14.7 14.7 0 0 1 0-4h4.6a14.7 14.7 0 0 1 0 4zm.3 5.6A15.6 15.6 0 0 0 16 16h3a8 8 0 0 1-4.4 3.6zM16.3 14a16 16 0 0 0 0-4h3.4a8 8 0 0 1 0 4z"/></svg>www.meridalehealth.com</li>
    </ul>

    <p class="address">418 Willow Crest Ave. Suite 120 Fairhaven, TX 75201</p>
  </section>

  <section class="card back" aria-label="Business card back">
    <div class="back-texture" role="img" aria-label="Embossed repeating brand pattern in glossy black"></div>
    <div class="brand">
      <span class="brand-dot"></span>
      <span class="brand-name">Meridale Health<br>Clinic</span>
    </div>
  </section>

</main>
</body>
</html>
```